Business Cards for company that supports physicians that do medical research

Need to create a business card for Qorvel Studies (www.qorvelstudies.example), a company devoted to supporting physicians who conduct medical research. The form of the card should match the message of research and information quest. I have provided the logo of the company as an uploaded file. Designs should be simple and slick aimed at very high end clients.

Target Market(s)

Medical doctors that are also researchers

Industry/Entity Type

Medical

Contact Information for Business Card

Should feature logo and fields for personal info:
Name/title
Phone /email

Font styles to use
Serif
Sans Serif

Requirements
Must have
• Qorvel logo and fields for personal info:
• Name: Bertrand Okonfu
• Title: VP Research and Senior Analyst
• Phone: 555-203-4719
• email: info@qorvelstudies.example
Nice to have
• Interesting cards that I've seen:
• 1- all black/charcoal or very dark background
• 2- Plastic - semi-transparent
• 3- non-standard height-width ratios
• 4- Functional cards -- USB drive incorporated
Should not have
• Too busy; needs to stay very simple

```html
<!DOCTYPE html>
<html lang="en">
<head>
<meta charset="UTF-8">
<title>Qorvel Studies – Business Card</title>
<link rel="stylesheet" href="https://fonts.googleapis.com/css2?family=Open+Sans:ital,wght@0,400;0,600;1,400&display=swap">
<style>
  :root {
    --backdrop: #383838;
    --card-white: #f7f7f7;
    --brand-blue: #1f7cc1;
    --ink-white: #ffffff;
  }
  html, body {
    margin: 0;
    width: 1200px;
    height: 750px;
    overflow: hidden;
    background: var(--backdrop);
    font-family: "Open Sans", Arial, sans-serif;
  }
  .stage {
    position: relative;
    width: 1200px;
    height: 750px;
  }
  .card {
    position: absolute;
    top: 228px;
    width: 461px;
    height: 262px;
    overflow: hidden;
  }
  .card--front { left: 124px; background: var(--card-white); }
  .card--back  { left: 618px; background: var(--brand-blue); }

  .front-panel {
    position: absolute;
    top: 0;
    right: 0;
    bottom: 0;
    left: 236px;
    background: var(--brand-blue);
  }

  .wordmark {
    position: absolute;
    font-weight: 600;
    text-align: center;
    line-height: 1;
  }
  .wordmark__name { display: block; }
  .wordmark__sub  { display: block; letter-spacing: 0.32em; }

  .card--front .wordmark {
    left: 30px;
    top: 98px;
    width: 150px;
    color: var(--brand-blue);
  }
  .card--front .wordmark__name { font-size: 40px; }
  .card--front .wordmark__sub  { font-size: 14px; margin-top: 6px; padding-left: 0.32em; }

  .contact {
    position: absolute;
    right: 26px;
    top: 86px;
    text-align: right;
    color: var(--ink-white);
  }
  .contact__name  { font-size: 16px; font-weight: 600; margin: 0; }
  .contact__title { font-size: 12px; margin: 2px 0 12px; }
  .contact__line {
    display: flex;
    justify-content: flex-end;
    align-items: center;
    gap: 7px;
    font-size: 11px;
    height: 17.5px;
  }
  .contact__icon { width: 12px; height: 12px; flex: none; }

  .card--back .wordmark {
    left: 0;
    right: 0;
    top: 92px;
    color: var(--ink-white);
  }
  .card--back .wordmark__name { font-size: 46px; }
  .card--back .wordmark__sub  { font-size: 17px; margin-top: 8px; padding-left: 0.32em; }
  .back-url {
    position: absolute;
    left: 0;
    right: 0;
    top: 209px;
    margin: 0;
    text-align: center;
    font-size: 10.5px;
    font-style: italic;
    letter-spacing: 0.14em;
    color: var(--ink-white);
  }
</style>
</head>
<body>
<main class="stage">

  <section class="card card--front" aria-label="Card front">
    <div class="front-panel"></div>

    <div class="wordmark">
      <span class="wordmark__name">Qorvel</span>
      <span class="wordmark__sub">STUDIES</span>
    </div>

    <div class="contact">
      <p class="contact__name">Bertrand Okonfu</p>
      <p class="contact__title">VP Research &amp; Senior Analyst</p>
      <div class="contact__line">
        <span>555-203-4719</span>
        <svg class="contact__icon" viewBox="0 0 24 24" aria-hidden="true"><path fill="#fff" d="M6.6 10.8a15.2 15.2 0 0 0 6.6 6.6l2.2-2.2c.3-.3.7-.4 1-.2 1.1.4 2.3.6 3.6.6.6 0 1 .4 1 1V20c0 .6-.4 1-1 1A17 17 0 0 1 3 4c0-.6.4-1 1-1h3.5c.6 0 1 .4 1 1 0 1.3.2 2.5.6 3.6.1.3 0 .7-.2 1z"/></svg>
      </div>
      <div class="contact__line">
        <span>info@qorvelstudies.example</span>
        <svg class="contact__icon" viewBox="0 0 24 24" aria-hidden="true"><rect x="2" y="5" width="20" height="14" fill="#fff"/><path d="M2 5l10 8 10-8" fill="none" stroke="var(--brand-blue)" stroke-width="1.6"/></svg>
      </div>
      <div class="contact__line">
        <span>www.qorvelstudies.example</span>
        <svg class="contact__icon" viewBox="0 0 24 24" aria-hidden="true"><circle cx="12" cy="12" r="10" fill="#fff"/><path d="M2 12h20M12 2c3 3 3 17 0 20M12 2c-3 3-3 17 0 20" fill="none" stroke="var(--brand-blue)" stroke-width="1.4"/></svg>
      </div>
    </div>
  </section>

  <section class="card card--back" aria-label="Card back">
    <div class="wordmark">
      <span class="wordmark__name">Qorvel</span>
      <span class="wordmark__sub">STUDIES</span>
    </div>
    <p class="back-url">www.qorvelstudies.example</p>
  </section>

</main>
</body>
</html>
```